Blow Dry Bar Business Cards

These cards must be eye catching and modern.
You must be willing to work fast and make changes.

Winner will be offered other projects

Files 1 THIS IS THE STYLE CARDS I AM INTRESTED IN!!!
Please be creative, I am paying for my own eye catching design. I need files to be nexa press ready.

COLORS THAT ARE PAINTED INSIDE MY SHOP:
- - - http://www.quorvelpaint.example/en/explore-colors/painter/color-selector.html?colors=4007-3C

- - - http://www.brandivex.example/color/paint-colors/hidden-corridor-d58-2

I want the business cards sleek and modern if you use the logo please correct imperfections. I added the part that says Blow Dry Bar (see website).
Do not be afraid to separate the blow dryer from the name to make the cards look like the file with the pink elephant.

SHOULD INCLUDE
*Blow Dryer (we are a blow dry bar not a salon we do not cut or color so do not include sheers of any kind)
*BUSINESS NAME: Simply Swept Upward - Blow Dry Bar (PLEASE SEE MY WEBSITE)
* Website: SIMPLYSWEPTUPWARD.EXAMPLE
*Phone number (555) 014-2763
Updates

Nexa press said it can be submitted in JPG

http://www.brandivex.example/color/paint-colors/hidden-corridor-d58-2 http://www.quorvelpaint.example/en/explore-colors/painter/color-selector.html?colors=4007-3C ^^^^ These links will take you to the color paint that is painted inside my shop.

Target Market(s)

AGES 18 - 55 WOMEN
HIGH END MARKET

Industry/Entity Type

Salon

Requirements
Must have
• SEE COLOR EXAMPLE FILE
BLOW DRYER
UNIQUE
I LIKE THE CARD WITH THE PINK ELEPHANT THE BEST
Nice to have
• BE AS CREATIVE AND MODERN AS POSSIBLE DO NOT COPY ANY OF THE CARDS BELOW.
Should not have
• SCISSORS
PINK

```html
<!DOCTYPE html>
<html lang="en">
<head>
<meta charset="utf-8">
<title>Simply Swept Upward — Blow Dry Bar Business Cards</title>
<link rel="stylesheet" href="https://fonts.googleapis.com/css2?family=Alfa+Slab+One&family=Lustria&family=Raleway:wght@400;500&display=swap">
<style>
  :root{
    --stage:#2b2622;
    --card-black:#0d0d0d;
    --card-black-soft:#1c1c1c;
    --gold:#d8c068;
    --gold-light:#f3e6a6;
    --gold-deep:#a88a32;
    --ink-dark:#2a2410;
    --contact:#e9e4d6;
    --rule:#8a8a8a;
  }
  *{margin:0;padding:0;box-sizing:border-box}
  html,body{width:1200px;height:885px;overflow:hidden;background:var(--stage)}
  .canvas{position:relative;width:1200px;height:885px;display:flex;flex-direction:column;align-items:center;justify-content:center;gap:60px}
  .card{position:relative;width:640px;height:366px;border-radius:10px;overflow:hidden;
    background:linear-gradient(160deg,var(--card-black-soft) 0%,var(--card-black) 60%);
    box-shadow:0 10px 30px rgba(0,0,0,.45)}

  /* Front */
  .front__name{position:absolute;left:40px;top:0;width:250px;height:296px;display:flex;align-items:center;justify-content:center;
    font-family:"Lustria",serif;font-size:40px;color:var(--gold);letter-spacing:1px;white-space:nowrap}
  .front__divider{position:absolute;left:310px;top:40px;width:1px;height:210px;background:var(--rule)}
  .front__info{position:absolute;left:340px;top:58px;right:24px}
  .front__title{font-family:"Alfa Slab One",serif;font-size:38px;line-height:1;
    background:linear-gradient(180deg,var(--gold-light),var(--gold) 55%,var(--gold-deep));
    -webkit-background-clip:text;background-clip:text;color:transparent;margin-bottom:30px}
  .contact{list-style:none;font-family:"Raleway",sans-serif;font-size:13px;color:var(--contact);text-transform:uppercase;letter-spacing:.5px}
  .contact li{display:flex;align-items:center;gap:10px;margin-bottom:13px;white-space:nowrap}
  .contact svg{width:16px;height:16px;flex:none}
  .front__band{position:absolute;left:0;right:0;bottom:0;height:70px;
    background:linear-gradient(180deg,var(--gold-light),var(--gold) 45%,var(--gold-deep));
    display:flex;align-items:center;justify-content:center;
    font-family:"Raleway",sans-serif;font-weight:500;font-size:15.5px;letter-spacing:.6px;color:var(--ink-dark);text-transform:uppercase;white-space:nowrap}

  /* Back */
  .back__pattern{position:absolute;left:0;right:0;height:118px;
    background:linear-gradient(135deg,#6f5a20 0%,#c9ad5a 30%,#1a1608 52%,#b99a45 75%,#5c4a18 100%)}
  .back__pattern--top{top:0}
  .back__pattern--bottom{bottom:0}
  .back__band{position:absolute;left:0;right:0;top:118px;height:130px;background:var(--card-black);
    border-top:2px solid var(--gold);border-bottom:2px solid var(--gold);
    display:flex;align-items:center;justify-content:center;gap:22px}
  .back__name{font-family:"Lustria",serif;font-size:50px;color:var(--gold);letter-spacing:1px;white-space:nowrap}
  .back__mark{width:26px;height:26px;border-radius:50%;background:var(--gold)}
</style>
</head>
<body>
<main class="canvas">

  <section class="card card--front" aria-label="Business card front">
    <div class="front__name">Swept Upward</div>
    <div class="front__divider"></div>
    <div class="front__info">
      <h1 class="front__title">Blow Dry Bar</h1>
      <ul class="contact">
        <li>
          <svg viewBox="0 0 16 16" aria-hidden="true"><path d="M4 1.5 6 5 4.6 6.4c.8 1.9 2.3 3.4 4.2 4.2L10.2 9.2 13.7 11l-.8 2.6c-.3.7-1 1-1.7.8C6.6 13.3 2.9 9.6 1.6 5 1.4 4.3 1.7 3.6 2.4 3.3Z" fill="var(--gold)"/></svg>
          (555) 014-2763
        </li>
        <li>
          <svg viewBox="0 0 16 16" aria-hidden="true"><circle cx="8" cy="8" r="6.5" fill="none" stroke="var(--gold)" stroke-width="1.4"/><ellipse cx="8" cy="8" rx="2.8" ry="6.5" fill="none" stroke="var(--gold)" stroke-width="1.1"/><line x1="1.5" y1="8" x2="14.5" y2="8" stroke="var(--gold)" stroke-width="1.1"/></svg>
          SIMPLYSWEPTUPWARD.EXAMPLE
        </li>
        <li>
          <svg viewBox="0 0 16 16" aria-hidden="true"><rect x="1.5" y="3.5" width="13" height="9" fill="var(--gold)"/><path d="M1.5 3.5 8 9l6.5-5.5" fill="none" stroke="var(--card-black)" stroke-width="1.1"/></svg>
          INFO@SIMPLYSWEPTUPWARD.EXAMPLE
        </li>
      </ul>
    </div>
    <div class="front__band">228 Harbor Reed Lane Suite 9 Maple Hollow, Texas 75001</div>
  </section>

  <section class="card card--back" aria-label="Business card back">
    <div class="back__pattern back__pattern--top" role="img" aria-label="Gold and black damask ornament pattern"></div>
    <div class="back__band">
      <span class="back__name">Swept Upward</span>
      <span class="back__mark" aria-hidden="true"></span>
    </div>
    <div class="back__pattern back__pattern--bottom" role="img" aria-label="Gold and black damask ornament pattern"></div>
  </section>

</main>
</body>
</html>
```